New Business card design to reflect rebrand

I would like a business card design with a good base colour for our new logo and also a placeholder for a profile pic of the card holder. the design needs to be editable to the point that we can easily change the picture of the person and use that design for printmerlo etc. we are looking at a metalic finish business card so will need a good base colour to bring out the finish.

Target Market(s)

prospective customers

Industry/Entity Type

Business

Contact Information for Business Card

I would like one editable design that we can change the name of the card holder and profile picture. The design need to be in a format that be send to printmerlo etc.

Our address is Fenwick Lodge, Copse Lane, Ashcombe Vale, GU14 3TP Tel no. 01483 556172

Requirements
Must have
• place holder for a profile pic for the card holder. in AI or preferably PSD format

```html
<!DOCTYPE html>
<html lang="en">
<head>
<meta charset="utf-8">
<title>Vantrell Facility Solutions – Business Card</title>
<link rel="stylesheet" href="https://fonts.googleapis.com/css2?family=Open+Sans:wght@400;600;700&display=swap">
<style>
  :root {
    --canvas-bg: #2b2d31;
    --brand-blue: #3f5573;
    --brand-blue-dark: #34475f;
    --card-white: #ffffff;
    --ink: #1f2329;
    --photo-top: #c9ced6;
    --photo-bottom: #2d3440;
  }
  * { box-sizing: border-box; margin: 0; padding: 0; }
  html, body {
    width: 1200px; height: 864px; overflow: hidden;
    background: var(--canvas-bg);
    font-family: "Open Sans", Arial, sans-serif;
  }
  .card {
    position: absolute;
    left: 300px;
    width: 600px;
    height: 343px;
    border-radius: 4px;
    overflow: hidden;
    box-shadow: 0 10px 24px rgba(0,0,0,.35);
  }
  /* Back face */
  .card--back {
    top: 60px;
    background: var(--brand-blue);
    color: var(--card-white);
  }
  .card--back .brand-name {
    position: absolute;
    left: 80px; top: 150px;
    font-weight: 700;
    line-height: 1;
  }
  .card--back .brand-name__main {
    display: block;
    font-size: 58px;
    letter-spacing: 4px;
  }
  .card--back .brand-name__sub {
    display: block;
    margin-top: 6px;
    font-size: 23px;
    letter-spacing: 5px;
  }
  /* Front face */
  .card--front {
    top: 461px;
    background: var(--card-white);
  }
  .profile-photo {
    position: absolute;
    left: 22px; top: 18px;
    width: 268px; height: 268px;
    background: linear-gradient(180deg, var(--photo-top) 0%, var(--photo-bottom) 100%);
  }
  .name-band {
    position: absolute;
    left: 0; right: 0; bottom: 0;
    height: 57px;
    background: var(--brand-blue);
  }
  .holder-name {
    position: absolute;
    left: 36px; bottom: 10px;
    color: var(--card-white);
    font-size: 30px;
    font-weight: 700;
  }
  .front-brand {
    position: absolute;
    left: 330px; top: 62px;
    color: var(--brand-blue);
    font-weight: 700;
    line-height: 1;
  }
  .front-brand__main {
    display: block;
    font-size: 38px;
    letter-spacing: 2px;
  }
  .front-brand__sub {
    display: block;
    margin-top: 5px;
    font-size: 15.5px;
    letter-spacing: 3.4px;
  }
  .contact {
    position: absolute;
    left: 330px; top: 168px;
    color: var(--ink);
    font-size: 14px;
    line-height: 1.55;
  }
  .contact__line { display: flex; align-items: center; gap: 8px; }
  .contact__icon { width: 12px; height: 12px; fill: var(--brand-blue-dark); }
  .contact__address { margin-top: 12px; font-size: 14.5px; line-height: 1.35; }
</style>
</head>
<body>

  <section class="card card--back" aria-label="Card back">
    <div class="brand-name">
      <span class="brand-name__main">VANTRELL</span>
      <span class="brand-name__sub">FACILITY SOLUTIONS</span>
    </div>
  </section>

  <section class="card card--front" aria-label="Card front">
    <div class="profile-photo" role="img" aria-label="Profile photo of the card holder"></div>
    <div class="name-band">
      <span class="holder-name">Alan Mercer</span>
    </div>

    <div class="front-brand">
      <span class="front-brand__main">VANTRELL</span>
      <span class="front-brand__sub">FACILITY SOLUTIONS</span>
    </div>

    <div class="contact">
      <div class="contact__line">
        <svg class="contact__icon" viewBox="0 0 24 24" aria-hidden="true"><path d="M6.6 10.8a15.1 15.1 0 0 0 6.6 6.6l2.2-2.2c.3-.3.7-.4 1-.2 1.1.4 2.3.6 3.6.6.6 0 1 .4 1 1V20c0 .6-.4 1-1 1A17 17 0 0 1 3 4c0-.6.4-1 1-1h3.5c.6 0 1 .4 1 1 0 1.3.2 2.5.6 3.6.1.3 0 .7-.2 1z"/></svg>
        <span>01483 556172</span>
      </div>
      <div class="contact__line">
        <svg class="contact__icon" viewBox="0 0 24 24" aria-hidden="true"><path d="M2 5h20v14H2z M2 5l10 8 10-8" fill="none" stroke="#34475f" stroke-width="2"/></svg>
        <span>info@vantrell.com</span>
      </div>
      <p class="contact__address">Fenwick Lodge, Copse Lane,<br>Ashcombe Vale, GU14 3TP</p>
    </div>
  </section>

</body>
</html>
```